Construction Company Cellar Crafters needs Business Card

I would like modern looking business card design. I am attaching logo of our company. Please include cell nr 302.418.7650 , email address cellarcrafters4u@examplemail.com, web : cellarcrafters4u.com, please also include wording: Specializing in finishing and remodeling basements. You can play with dark grey and orange colors or any ideas are welcome. Also include social media icons Friendloop and HouseGuidr.

```html
<!DOCTYPE html>
<html lang="en">
<head>
<meta charset="UTF-8">
<title>Cellar Crafters — Business Card</title>
<link rel="stylesheet" href="https://fonts.googleapis.com/css2?family=Open+Sans:wght@400;600;700&display=swap">
<style>
  :root {
    --backdrop: #3b3431;
    --card: #141414;
    --card-edge: #1f1f1f;
    --orange: #f26a21;
    --white: #f2f2f2;
    --silver: #c9c9c9;
    --divider: #5a3018;
  }
  * { box-sizing: border-box; margin: 0; padding: 0; }
  html, body {
    width: 1200px; height: 900px; overflow: hidden;
    background: var(--backdrop);
    font-family: "Open Sans", Arial, sans-serif;
  }
  .stage {
    position: relative; width: 1200px; height: 900px;
    display: flex; align-items: center; justify-content: center; gap: 50px;
  }
  .card {
    position: relative; width: 525px; height: 300px;
    background: var(--card);
    border: 1px solid var(--card-edge);
    box-shadow: 0 10px 30px rgba(0,0,0,.45);
  }

  /* Front */
  .brand-mark {
    position: absolute; left: 36px; top: 100px; width: 190px;
    display: flex; align-items: center; gap: 10px;
  }
  .brand-mark .square { width: 14px; height: 14px; background: var(--orange); flex: none; }
  .brand-mark .name {
    color: var(--orange); font-weight: 700; font-size: 24px; line-height: 1.1;
  }
  .divider {
    position: absolute; left: 236px; top: 38px; width: 1px; height: 150px;
    background: var(--divider);
  }
  .contact { position: absolute; left: 258px; top: 36px; right: 14px; }
  .contact .person { color: var(--orange); font-weight: 700; font-size: 15px; }
  .contact .role { color: var(--white); font-size: 11.5px; margin-bottom: 22px; }
  .contact-line {
    display: flex; align-items: center; gap: 8px;
    color: var(--white); font-size: 11.5px; line-height: 17px;
  }
  .contact-line svg { width: 10px; height: 10px; flex: none; fill: var(--orange); }
  .socials { display: flex; gap: 14px; margin-top: 12px; }
  .social { color: var(--orange); font-weight: 600; font-size: 11.5px; }
  .tagline {
    position: absolute; left: 36px; bottom: 30px;
    color: var(--orange); font-size: 12.5px; letter-spacing: .3px; text-transform: uppercase;
  }

  /* Back */
  .back-brand {
    position: absolute; inset: 0;
    display: flex; align-items: center; justify-content: center;
  }
  .back-brand .name {
    font-family: "Open Sans", Arial, sans-serif;
    color: var(--silver); font-weight: 600; font-size: 30px;
  }
</style>
</head>
<body>
<main class="stage">
  <section class="card card-front">
    <div class="brand-mark">
      <span class="square"></span>
      <span class="name">Cellar Crafters</span>
    </div>
    <div class="divider"></div>
    <div class="contact">
      <p class="person">Daniel Mercer</p>
      <p class="role">Managing Director</p>
      <p class="contact-line">
        <svg viewBox="0 0 10 10"><path d="M2 0.5 L3.6 2.6 L2.7 3.6 Q3.8 5.9 6.4 7.3 L7.4 6.4 L9.5 8 L8.4 9.5 Q4.6 9.3 0.5 1.6 Z"/></svg>
        302.418.7650
      </p>
      <p class="contact-line">
        <svg viewBox="0 0 10 10"><path d="M0.5 2 H9.5 V8.5 H0.5 Z"/><path d="M1 2.6 L5 5.6 L9 2.6" stroke="#141414" stroke-width="0.8" fill="none"/></svg>
        cellarcrafters4u@examplemail.com
      </p>
      <p class="contact-line">
        <svg viewBox="0 0 10 10"><circle cx="5" cy="5" r="4.5"/><path d="M0.7 5 H9.3 M5 0.6 Q2.5 5 5 9.4 M5 0.6 Q7.5 5 5 9.4" stroke="#141414" stroke-width="0.7" fill="none"/></svg>
        cellarcrafters4u.com
      </p>
      <div class="socials">
        <span class="social">Friendloop</span>
        <span class="social">HouseGuidr</span>
      </div>
    </div>
    <p class="tagline">Specializing in finishing and remodeling basements.</p>
  </section>

  <section class="card card-back">
    <div class="back-brand">
      <span class="name">Cellar Crafters</span>
    </div>
  </section>
</main>
</body>
</html>
```